Website Redesign - We Need Your Magic!

Hello we are looking for you to help us re-design a high end and professional website for a high-end private school.

Here is the current site: http://www.ferndalecrest.com/

NOTE THIS IS DESIGN ONLY, NO CODING :)

The image they want to portray is that of high quality sports and education, in a creative "un-stiff" way.

Menu Bar: Horizontal

Look and Feel:

Site Colors: Dark green and a Gold yellow (logos are attached)

This site will represent a school so the look must be clean, bold, and classy. The site must have a very clean user interface, with things easily recognizable. Think simple.

The site should be visually appealing! If you come to me with templates, or a ton of text you will be out.

This site should be outside the box, we do not want boring, we do not want status quo. This site should instill excitement, innovation, and athletics.

So the main points again are:

1. High-end and classy look, with creative feel
2. Simple and clear navigation style
3. To cover the Junior and High School - Ferndale Crest College Schools

Think outside the box. We look forward to seeing what you come up with!!

Thank you for helping us create an amazing site for the school!

Industry/Entity Type

School

```html
<!DOCTYPE html>
<html lang="en">
<head>
<meta charset="utf-8">
<title>Ferndale Crest College</title>
<link href="https://fonts.googleapis.com/css2?family=Roboto:wght@400;500;700&display=swap" rel="stylesheet">
<style>
:root{
  --green-dark:#0d5a26;
  --green:#14692e;
  --green-ribbon:#1a7032;
  --gold:#f6ea1c;
  --gold-deep:#e9d800;
  --white:#ffffff;
  --text:#222;
  --tab-grey:#dcdcdc;
}
*{box-sizing:border-box;margin:0;padding:0}
html,body{width:1200px;height:1200px;overflow:hidden}
body{
  font-family:'Roboto',Arial,sans-serif;
  background:radial-gradient(ellipse 70% 55% at 50% 45%,#3f9a4d 0%,#2a7f3a 45%,#1d6a2f 100%);
  position:relative;color:var(--text);
}
.abs{position:absolute}
.topbar{left:0;top:0;width:1200px;height:6px;background:var(--gold)}
.contact-tab{left:583px;top:0;width:437px;height:21px;background:var(--gold);border-radius:0 0 22px 22px;
  display:flex;align-items:center;justify-content:center;gap:14px;font-size:10.5px;color:var(--green-dark)}
.contact-tab span{display:flex;align-items:center;gap:5px}
.brand{left:197px;top:74px;display:flex;align-items:center;gap:10px;color:var(--gold);font-weight:700;font-size:22px;line-height:1.1;width:170px}
.brand .dot{width:34px;height:34px;border-radius:50%;background:var(--gold);flex:none}
.tagline{left:357px;top:140px;font-size:14.5px;font-weight:700;color:var(--gold);display:flex;gap:10px;align-items:center;letter-spacing:.2px}
.tagline i{width:5px;height:5px;border-radius:50%;background:#4e9a55;display:inline-block}
.login{left:949px;top:49px;width:92px;height:31px;background:var(--green);color:#fff;font-size:11.5px;display:flex;align-items:center;justify-content:center;gap:7px;box-shadow:0 2px 4px rgba(0,0,0,.35)}
.search{left:847px;top:133px;width:196px;height:30px;display:flex}
.search .field{flex:1;background:#fff;display:flex;align-items:center;gap:8px;padding-left:10px;color:#aaa;font-style:italic;font-size:12px}
.search .btn{width:62px;background:var(--gold);color:var(--green-dark);font-size:11px;font-weight:700;display:flex;align-items:center;justify-content:center}
.ribbon{left:114px;top:206px;width:1010px;height:43px}
.nav{left:148px;top:188px;width:940px;height:45px;background:var(--green);display:flex;box-shadow:0 3px 6px rgba(0,0,0,.3)}
.nav a{color:#fff;text-decoration:none;font-size:13px;display:flex;align-items:center;justify-content:center;gap:8px;border-right:1px solid #0a4a1e;position:relative}
.nav a:last-child{border-right:none}
.nav a.active::after{content:"";position:absolute;left:28px;right:27px;bottom:0;height:3px;background:var(--gold)}
.nav .caret{width:0;height:0;border-left:4px solid transparent;border-right:4px solid transparent;border-top:4px solid var(--gold)}
.hero{left:158px;top:233px;width:922px;height:322px;background:linear-gradient(100deg,#6b8a5a 0%,#9bb07c 35%,#c9c3a0 60%,#8d9a6a 100%)}
.hero-panel{left:194px;top:233px;width:408px;height:322px;background:rgba(31,110,50,.88);padding:64px 28px 0 28px;color:#fff}
.hero-panel .pre{font-size:13.5px;letter-spacing:1px;font-weight:500}
.hero-panel h1{font-size:27px;font-weight:700;margin-top:8px;padding-bottom:8px;border-bottom:3px solid var(--gold);width:348px}
.hero-panel p{font-size:13.2px;line-height:22.3px;margin-top:6px;width:354px}
.learn{margin-top:20px;margin-left:2px;width:121px;height:34px;background:var(--gold);color:var(--green-dark);font-weight:500;font-size:13px;display:flex;align-items:center;justify-content:center;border-radius:2px}
.dots{display:flex;gap:5px;margin-top:21px;margin-left:5px}
.dots i{width:14px;height:14px;border-radius:50%;background:#ccc}
.dots i:first-child{background:var(--gold)}
.features{left:158px;top:555px;width:922px;height:131px;background:var(--green);display:flex;box-shadow:0 3px 6px rgba(0,0,0,.3)}
.feature{flex:1;display:flex;align-items:flex-start;padding:20px 0 0 20px;gap:26px;border-right:1px solid #0c5222;color:#fff}
.feature:last-child{border-right:none}
.feature .icon{width:50px;height:40px;margin-top:24px;flex:none}
.feature h3{font-size:12.5px;letter-spacing:1px;font-weight:700;border-bottom:2px solid var(--gold);padding-bottom:5px;width:178px}
.feature p{font-size:10.8px;line-height:13.7px;margin-top:10px;width:186px}
.feature .more{color:var(--gold);font-size:11px;font-weight:500;margin-top:9px}
.main-frame{left:153px;top:711px;width:646px;height:500px;background:rgba(255,255,255,.18)}
.main{left:162px;top:720px;width:628px;height:490px;background:#fff;padding:20px 28px 0 18px}
.main h2{font-size:14.5px;color:var(--green);font-weight:400;letter-spacing:1px;border-bottom:2px solid var(--gold-deep);width:532px;padding-bottom:8px}
.main p{font-size:11.4px;line-height:14.6px;letter-spacing:.85px;color:#333;margin-top:14px}
.main h2.second{margin-top:34px}
.head-note{display:flex;gap:16px;margin-top:28px}
.portrait{width:198px;height:173px;background:linear-gradient(135deg,#0f5a45,#2f6d5a 55%,#b79a7a);flex:none}
.head-note p{margin-top:0;text-align:justify}
.head-note p + p{margin-top:11px}
.sidebox{background:#fff}
.sidebox .title{background:var(--gold);color:var(--green-dark);font-size:13px;font-weight:500;height:40px;display:flex;align-items:center;padding-left:18px}
.calendar{left:812px;top:714px;width:267px;height:332px}
.tabs{display:flex;background:var(--tab-grey);height:24px;font-size:12.5px;font-weight:500;color:var(--green)}
.tabs span{display:flex;align-items:center;padding:0 8px 0 10px}
.tabs span.on{background:#fff;padding:0 9px 0 6px}
.tabs span:last-child{padding-left:10px}
.event{display:flex;gap:12px;align-items:flex-start;height:89px;padding:15px 0 0 16px;border-bottom:1px solid #ddd}
.event:last-child{border-bottom:none}
.date{width:56px;height:55px;background:var(--green);flex:none;text-align:center;color:#fff}
.date .m{font-size:12px;height:20px;line-height:20px;border-bottom:2px solid #fff}
.date .d{font-size:20px;font-weight:700;color:var(--gold);line-height:33px}
.event b{font-size:12px;font-weight:500;display:block;margin-top:12px}
.event small{font-size:12px;display:block;margin-top:6px;color:#333}
.sports{left:812px;top:1065px;width:267px;height:150px}
.sports ul{list-style:none;padding:14px 20px 0 14px;font-size:12px}
.sports li b{font-weight:500;display:flex;justify-content:space-between}
.sports li b::before{content:"•";margin-right:6px}
.sports li p{padding-left:10px;text-align:justify;line-height:15px;margin-top:4px;color:#333}
</style>
</head>
<body>
<div class="abs topbar"></div>
<div class="abs contact-tab">
  <span>Ferndale Crest College</span>
  <span><svg width="12" height="9" viewBox="0 0 12 9"><rect x=".5" y=".5" width="11" height="8" fill="none" stroke="#0d5a26"/><path d="M.5 .5 6 5l5.5-4.5" fill="none" stroke="#0d5a26"/></svg>office@ferndalecrest.com</span>
  <span><svg width="11" height="11" viewBox="0 0 11 11"><circle cx="5.5" cy="5.5" r="5" fill="none" stroke="#0d5a26"/><path d="M3.5 3c0 2.5 2 4.5 4.5 4.5" stroke="#0d5a26" fill="none" stroke-width="1.4"/></svg>0700.555.101 - 0700.555.202</span>
</div>

<div class="abs brand"><span class="dot"></span>Ferndale Crest</div>

<div class="abs tagline">STEPPING AHEAD IN <i></i> EDUCATION <i></i> CULTURE <i></i> SPORT <i></i> LIFE</div>

<div class="abs login">Staff Login
  <svg width="11" height="14" viewBox="0 0 11 14"><path d="M2.5 6V4a3 3 0 0 1 6 0v2" fill="none" stroke="#fff" stroke-width="1.6"/><rect x="0" y="6" width="11" height="8" rx="1" fill="#fff"/><rect x="4.8" y="8.5" width="1.4" height="3" fill="#14692e"/></svg>
</div>

<div class="abs search">
  <div class="field"><svg width="11" height="11" viewBox="0 0 11 11"><circle cx="4.5" cy="4.5" r="3.6" fill="none" stroke="#ccc" stroke-width="1.5"/><path d="M7.2 7.2 10.5 10.5" stroke="#ccc" stroke-width="1.5"/></svg>Search...</div>
  <div class="btn">SEARCH</div>
</div>

<svg class="abs ribbon" viewBox="0 0 1010 43">
  <polygon points="0,0 40,10 40,43 0,43 20,21" fill="#1a7032"/>
  <polygon points="1010,0 970,10 970,43 1010,43 990,21" fill="#1a7032"/>
</svg>

<nav class="abs nav">
  <a class="active" style="width:104px">Home</a>
  <a style="width:108px">About Us <i class="caret"></i></a>
  <a style="width:123px">Academics <i class="caret"></i></a>
  <a style="width:86px">Sports <i class="caret"></i></a>
  <a style="width:156px">Joining Ferndale Crest</a>
  <a style="width:182px">Working at the College</a>
  <a style="width:181px">Contact Us</a>
</nav>

<div class="abs hero" role="img" aria-label="Photo of girls running on a sports field"></div>
<div class="abs hero-panel">
  <div class="pre">WELCOME TO</div>
  <h1>FERNDALE CREST COLLEGE</h1>
  <p>Welcome to Ferndale Crest Group of Schools where our School Motto is 'Concordia' meaning Togetherness. We aim to work together in every aspect of School life, from academics to sport.</p>
  <div class="learn">Learn More</div>
  <div class="dots"><i></i><i></i><i></i></div>
</div>

<section class="abs features">
  <div class="feature">
    <svg class="icon" viewBox="0 0 50 40"><circle cx="17" cy="9" r="7" fill="#fff"/><path d="M3 32c0-9 6-14 14-14s12 4 13 8" fill="#fff"/><circle cx="30" cy="15" r="7" fill="#f6ea1c"/><path d="M17 40c0-9 5-15 13-15s13 6 13 15z" fill="#f6ea1c"/></svg>
    <div><h3>ABOUT US</h3><p>Lorem ipsum dolor sit amet, consectetur adipisicing elit, sed do eiusmod tempor incididunt ut</p><div class="more">Learn more»</div></div>
  </div>
  <div class="feature">
    <svg class="icon" viewBox="0 0 50 40"><path d="M6 8 14 4v26l-8 4z" fill="#fff"/><path d="M15 10l16-6v26l-16 6z" fill="#f6ea1c"/><path d="M18 12l10-4" stroke="#14692e" stroke-width="1.5"/></svg>
    <div><h3>WHAT WE DO</h3><p>Lorem ipsum dolor sit amet, consectetur adipisicing elit, sed do eiusmod tempor incididunt ut</p><div class="more">Learn more»</div></div>
  </div>
  <div class="feature">
    <svg class="icon" viewBox="0 0 50 40"><circle cx="8" cy="4" r="3.5" fill="#fff"/><path d="M3 9h10l8-4 1 2-8 5v26h-3V26H9v12H6V14H3z" fill="#fff"/><rect x="24" y="2" width="24" height="17" fill="none" stroke="#f6ea1c" stroke-width="2"/></svg>
    <div><h3>OTHER TITLE</h3><p>Lorem ipsum dolor sit amet, consectetur adipisicing elit, sed do eiusmod tempor incididunt ut</p><div class="more">Learn more»</div></div>
  </div>
</section>

<div class="abs main-frame"></div>
<article class="abs main">
  <h2>Welcome to Ferndale Crest College</h2>
  <p>Welcome to Ferndale Crest Group of Schools where our School Motto is 'Concordia' meaning Togetherness. We aim to work together in every aspect of School life, from academics to sport.</p>
  <p>Ferndale Crest College opened on 14th February 1983 and occupies 120 ha of land amidst the low hills of the Ashwood Range, 8km west of Millbrook. This location encourages focus on School life away from the distractions and hustle and bustle of the larger towns.</p>
  <p>The day scholars have the option of selected bus drop off points for parents to collect day scholars closer to home. Ferndale Crest College offers a wide range of academic subjects alongside a varied sport and extra-curricular program.</p>
  <h2 class="second">Headmaster's Welcome Note</h2>
  <div class="head-note">
    <div class="portrait" role="img" aria-label="Portrait photo of the headmaster"></div>
    <div>
      <p>Welcome to Ferndale Crest College. Here at the College we aim to encourage each pupil to be a self-confident, well-rounded individual. We aim to propel them to the highest level of achievement in both academics and extra-curricular activities to provide them with the life skills they will need when they leave the College and to prepare them to be of value to society.</p>
      <p>The College is a warm community which lives out high standards and is rightly proud of its achievements. We are a small enough School for each pupil to be known well, but large enough to offer a wide range of subjects and experience.</p>
    </div>
  </div>
</article>

<aside class="abs sidebox calendar">
  <div class="title">School Calender</div>
  <div class="tabs"><span class="on">First Term</span><span>Second Term</span><span>Third Term</span></div>
  <div class="event"><div class="date"><div class="m">Jan</div><div class="d">14</div></div><div><b>Begins:</b><small>Tuesday 14th January</small></div></div>
  <div class="event"><div class="date"><div class="m">Jan</div><div class="d">31</div></div><div><b>1st Fixture Free:</b><small>Friday 31st y</small></div></div>
  <div class="event"><div class="date"><div class="m">Feb</div><div class="d">3</div></div><div><b>Second Fixture Free:</b><small>Monday 3rd February</small></div></div>
</aside>

<aside class="abs sidebox sports">
  <div class="title">Sports Announcements</div>
  <ul>
    <li><b><span style="margin-right:auto">Rugby</span><span>-</span></b>
      <p>Lorem ipsum dolor sit amet, consectetur adipisicing elit, sed do eiusmod tempor incididunt ut labore et dolore magna aliqua.</p></li>
  </ul>
</aside>
</body>
</html>
```